Luxury travel agency needs a website design

We are a travel agency specializing in booking luxury vacations. We specialize in Hawaii, Europe and Caribbean, but will do all vacations. I want a very classy website design which would attract luxury clients. The company name is "Harbors and Hammocks Travel Agency". Would love the web design to go with the color scheme of the logo. Hex codes included in files. Logo is attached. Would also love more Grey in the website. I want it very elegant

Coding

Coded - Design and coding required

Font styles to use
Sans Serif
Decorative

Requirements
Must have
• - Consultation Tab or a page where the client can fill out a short form about what vacation that they would want to book. I want this info to be sent to me in order for me to contact them.
- Somewhere with my contact info "email: marla@harborsandhammockstravel.example and phone number"
- Social media links
- About section "Marla Dunbevy - Agency Owner (picture provided)
Marla has been traveling full time for the passed two years and has been very passionate about travel from a young age. Marla is dedicated to working closely with clients to book their dream vacation.
Marla's specializations include honeymoons and anniversaries focusing on travel in Europe, Hawaii and all inclusive resorts in the Caribbean.

```html
<!DOCTYPE html>
<html lang="en">
<head>
<meta charset="utf-8">
<title>Schedule a Consult – Harbors &amp; Hammocks Travel Agency</title>
<link rel="stylesheet" href="https://fonts.googleapis.com/css2?family=Montserrat:wght@400;500;600&family=Rye&display=swap">
<style>
:root{
  --orange:#F0894E;
  --ink:#2f2f2f;
  --dark:#0b0b0b;
  --page:#f7f7f7;
  --white:#ffffff;
  --muted:#8a8a8a;
  --label:#222;
}
*{box-sizing:border-box;margin:0;padding:0}
html,body{width:1200px;height:2700px;overflow:hidden}
body{position:relative;background:var(--page);font-family:"Montserrat",sans-serif;color:var(--label)}
.abs{position:absolute}

.topbar{left:0;top:0;width:1200px;height:45px;background:var(--orange);color:var(--white);font-size:13px;font-weight:500}
.topbar .mail{left:172px;top:13px;display:flex;align-items:center;gap:8px}
.topbar .phone{left:730px;top:13px;display:flex;align-items:center;gap:8px}
.topbar .socials{left:880px;top:11px;display:flex;gap:12px}
.topbar .socials span{width:20px;height:20px;border-radius:50%;background:var(--white);display:block}

.hero{left:0;top:45px;width:1200px;height:500px}
.palm{left:0;top:440px;width:125px;height:165px;background:linear-gradient(135deg,#3e7a32,#1f4d1c);border-radius:0 80% 0 0;opacity:.9}

.brand{left:172px;top:95px;width:260px;text-align:center;font-family:"Montserrat",sans-serif;font-weight:600;color:var(--ink)}
.brand .name{font-size:22px;letter-spacing:.5px;display:flex;align-items:center;gap:8px;justify-content:center}
.brand .name i{width:14px;height:14px;background:var(--orange);border-radius:50%;display:block}
.brand .sub{font-size:10px;letter-spacing:3px;margin-top:4px}

.nav{top:108px;font-size:16px;color:#111;font-weight:500}
.nav.home{left:555px}.nav.about{left:646px}.nav.contact{left:746px}
.cta{left:853px;top:93px;width:173px;height:51px;border-radius:26px;background:#3b3b3b;color:var(--white);font-size:13px;font-weight:600;display:flex;align-items:center;justify-content:center}

.hero-title{right:174px;top:235px;text-align:right;font-family:"Rye",serif;color:var(--white);font-size:52px;line-height:76px;text-shadow:0 2px 6px rgba(0,0,0,.25)}

.section-title{left:0;width:1200px;top:650px;text-align:center;font-family:"Rye",serif;font-size:40px;color:var(--ink)}
.section-title em{font-style:normal;color:var(--orange)}
.intro{left:170px;width:860px;top:728px;text-align:center;font-size:12.5px;line-height:26px;color:#333}

.label{left:172px;font-size:14px;font-weight:500;color:var(--label)}
.label b{color:#e02020;font-weight:500}
.field{height:61px;border-radius:31px;background:var(--white);box-shadow:0 2px 6px rgba(0,0,0,.18);border:1px solid #e6e6e6;font-size:14px;color:var(--muted);padding-left:21px;display:flex;align-items:center}
.half-l{left:172px;width:417px}.half-r{left:609px;width:417px}.full{left:172px;width:855px}
.field .caret{position:absolute;right:20px;top:24px;width:0;height:0;border-left:6px solid transparent;border-right:6px solid transparent;border-top:9px solid #111}

.submit{left:538px;top:1589px;width:124px;height:54px;border-radius:27px;background:var(--orange);color:var(--white);font-size:16px;font-weight:600;display:flex;align-items:center;justify-content:center}
.camera{left:470px;top:1660px;width:88px;height:70px;background:linear-gradient(135deg,#3a4a55,#1c2328);border-radius:12px;transform:rotate(-18deg)}

.band{left:0;top:1770px;width:1200px;height:470px}
.band-name{left:0;width:1200px;top:1895px;text-align:center;color:var(--white);font-family:"Montserrat",sans-serif;font-weight:600}
.band-name .n{font-size:60px;letter-spacing:1px}
.band-name .s{font-size:20px;letter-spacing:7px;margin-top:4px}

.footer{left:0;top:2240px;width:1200px;height:460px;background:var(--dark)}
.foot-brand{left:172px;top:2395px;width:310px;color:var(--white);text-align:center;font-weight:600}
.foot-brand .n{font-size:28px;display:flex;align-items:center;gap:10px;justify-content:center}
.foot-brand .n i{width:18px;height:18px;border-radius:50%;background:var(--white);display:block}
.foot-brand .s{font-size:11px;letter-spacing:3px;margin-top:6px}
.rope{left:-20px;top:2480px;width:84px;height:84px;border-radius:50%;background:radial-gradient(circle,#a88a5e 0 30%,#d8b98a 60%,#c4a170)}
.foot-h{color:var(--white);font-size:19px;font-weight:500;line-height:27px;letter-spacing:.3px}
.links{left:571px;top:2326px;color:var(--white);font-size:14px;line-height:28.6px}
.news-text{left:781px;top:2344px;width:250px;color:var(--white);font-size:14px;line-height:23px}
.news-input{left:781px;top:2410px;width:246px;height:56px;border-radius:28px;background:var(--white);color:#222;font-size:14px;padding-left:21px;display:flex;align-items:center}
.news-btn{left:781px;top:2478px;width:126px;height:56px;border-radius:28px;background:var(--orange);color:var(--white);font-size:14px;font-weight:500;display:flex;align-items:center;justify-content:center}
.rule{left:172px;top:2606px;width:855px;height:2px;background:#e8e8e8}
.copy{left:0;width:1200px;top:2650px;text-align:center;color:var(--white);font-size:14px}
</style>
</head>
<body>

<header>
  <div class="abs topbar">
    <div class="abs mail">
      <svg width="17" height="12" viewBox="0 0 17 12"><rect x="1" y="1" width="15" height="10" fill="none" stroke="#fff" stroke-width="1.4"/><path d="M1 1l7.5 6L16 1" fill="none" stroke="#fff" stroke-width="1.4"/></svg>
      marla@harborsandhammockstravel.example
    </div>
    <div class="abs phone">
      <svg width="18" height="18" viewBox="0 0 24 24"><path d="M6.6 10.8a15 15 0 006.6 6.6l2.2-2.2a1 1 0 011-.25 11.4 11.4 0 003.6.6 1 1 0 011 1V20a1 1 0 01-1 1A17 17 0 013 4a1 1 0 011-1h3.5a1 1 0 011 1c0 1.25.2 2.45.6 3.6a1 1 0 01-.25 1z" fill="none" stroke="#fff" stroke-width="1.6"/></svg>
      (555)014-2277
    </div>
    <div class="abs socials" aria-label="Social media links"><span></span><span></span><span></span><span></span><span></span></div>
  </div>

  <svg class="abs hero" width="1200" height="500" viewBox="0 0 1200 500" role="img" aria-label="Sunset over a calm sea with rocky shore and green headland">
    <defs>
      <linearGradient id="sky" x1="0" y1="0" x2="0" y2="1">
        <stop offset="0" stop-color="#c9a6b8"/>
        <stop offset=".35" stop-color="#f2c3a8"/>
        <stop offset=".55" stop-color="#f6d2a2"/>
        <stop offset=".7" stop-color="#a9c4d6"/>
        <stop offset="1" stop-color="#5f8fb0"/>
      </linearGradient>
    </defs>
    <path d="M0 0H1200V400Q880 530 620 495Q300 470 0 420Z" fill="url(#sky)"/>
  </svg>
  <div class="abs palm" role="img" aria-label="Palm frond"></div>

  <div class="abs brand">
    <div class="name"><i></i>HARBORS &amp; HAMMOCKS</div>
    <div class="sub">TRAVEL AGENCY</div>
  </div>
  <nav>
    <div class="abs nav home">HOME</div>
    <div class="abs nav about">ABOUT</div>
    <div class="abs nav contact">CONTACT</div>
    <div class="abs cta">SCHEDULE A CONSULT</div>
  </nav>
  <h1 class="abs hero-title">SCHEDULE A<br>CONSULT</h1>
</header>

<main>
  <h2 class="abs section-title">SCHEDULE <em>A CONSULT</em></h2>
  <p class="abs intro">Nemo enim ipsam voluptatem quia voluptas sit aspernatur aut odit aut fugit, sed quia consequuntur magni dolores eos qui ratione voluptatem sequi nesci unt. Neque porro quisquam est, qui dolorem ipsum quia dolor sit amet.</p>

  <div class="abs label" style="top:806px">Full Name<b>*</b></div>
  <div class="abs field half-l" style="top:843px">First Name</div>
  <div class="abs field half-r" style="top:843px">Last Name</div>

  <div class="abs label" style="top:933px">Phone Number<b>*</b></div>
  <div class="abs field half-l" style="top:970px">Area Code</div>
  <div class="abs field half-r" style="top:970px">Phone Number</div>

  <div class="abs label" style="top:1060px">E-mail<b>*</b></div>
  <div class="abs field full" style="top:1098px">ex.myname@example.com</div>

  <div class="abs label" style="top:1188px">Company or Organization Name</div>
  <div class="abs field full" style="top:1226px"></div>

  <div class="abs label" style="top:1315px">Consultation Interest</div>
  <div class="abs field full" style="top:1353px">Select an option<span class="caret"></span></div>

  <div class="abs label" style="top:1442px">Desired Date for Consultation Call</div>
  <div class="abs field full" style="top:1480px">Desired Date for Consultation Call</div>

  <div class="abs submit">SUBMIT</div>
  <div class="abs camera" role="img" aria-label="Vintage camera on a strap"></div>
</main>

<footer>
  <svg class="abs band" width="1200" height="470" viewBox="0 0 1200 470" role="img" aria-label="Aerial view of a green tropical island coastline at sunset">
    <defs>
      <linearGradient id="isle" x1="0" y1="0" x2="0" y2="1">
        <stop offset="0" stop-color="#3f6f98"/>
        <stop offset=".35" stop-color="#7f8fa0"/>
        <stop offset=".55" stop-color="#3d5a2c"/>
        <stop offset=".8" stop-color="#4f6f7f"/>
        <stop offset="1" stop-color="#2f4f68"/>
      </linearGradient>
    </defs>
    <rect width="1200" height="470" fill="url(#isle)"/>
  </svg>
  <div class="abs band-name">
    <div class="n">HARBORS &amp; HAMMOCKS</div>
    <div class="s">TRAVEL AGENCY</div>
  </div>
  <svg class="abs" style="left:0;top:2115px" width="1200" height="135" viewBox="0 0 1200 135">
    <path d="M0 117Q600 -60 1200 117V135H0Z" fill="var(--orange)"/>
    <path d="M0 135Q600 -35 1200 125V135Z" fill="var(--dark)"/>
  </svg>
  <div class="abs footer"></div>

  <div class="abs foot-brand">
    <div class="n"><i></i>HARBORS &amp; HAMMOCKS</div>
    <div class="s">TRAVEL AGENCY</div>
  </div>
  <div class="abs rope" role="img" aria-label="Coiled rope"></div>

  <div class="abs foot-h" style="left:570px;top:2277px">QUICK LINKS</div>
  <div class="abs links">Home<br>About Us<br>Blog<br>Destinations<br>Travel<br>Contact Us</div>

  <div class="abs foot-h" style="left:780px;top:2277px">SUBSCRIBE TO OUR<br>NEWSLETTER</div>
  <p class="abs news-text">Etiam rhoncus. Maecenas temp us, tellus eget condimentum rho</p>
  <div class="abs news-input">Email</div>
  <div class="abs news-btn">SUBSCRIBE</div>

  <div class="abs rule"></div>
  <div class="abs copy">Copyrights @ 2021 Harbors and Hammocks. All Rights Reserved.</div>
</footer>

</body>
</html>
```